Modern Attractive Letterhead for Veterinary House Call Business.

A letterhead which can be printed on A4, A5 and A6 paper sizes.
To have: ( our files to be uploaded)
1. Logo with Text
2. telephone
3. email
4. website
5. Address

Target Market(s)

60-85year mainly women pet owners. Also market include families, young professionals, busy people who have dogs and cats

Industry/Entity Type

Business

Requirements
Must have
• 1. Logo with Text ( provided)
• 2. telephone
• 3. email
• 4. website
• 5. Address
Nice to have
• Needs to be modern, preferably warm and caring in nature( if possible )
Should not have
• difficulty in printing A5 and A6

```html
<!DOCTYPE html>
<html lang="en">
<head>
<meta charset="utf-8">
<title>Hearthside Vet Care — Letterhead</title>
<link href="https://fonts.googleapis.com/css2?family=Cinzel:wght@400;600&display=swap" rel="stylesheet">
<style>
  :root {
    --brand-teal: #2a6fa8;
    --brand-green: #3f9a3a;
    --ink: #2b2b33;
    --paper-top: #ffffff;
    --paper-bottom: #f1f1f4;
    --mark-tint: #e4ebf3;
  }
  html, body {
    margin: 0;
    padding: 0;
    width: 949px;
    height: 1200px;
    overflow: hidden;
    background: #ffffff;
  }
  .letterhead {
    position: relative;
    width: 949px;
    height: 1200px;
    background: linear-gradient(160deg, var(--paper-top) 0%, var(--paper-top) 35%, var(--paper-bottom) 100%);
    font-family: "Cinzel", "Times New Roman", serif;
    color: var(--ink);
  }
  .brand {
    position: absolute;
    top: 92px;
    left: 0;
    right: 0;
    display: flex;
    justify-content: center;
    align-items: center;
    gap: 14px;
  }
  .brand-dot {
    width: 22px;
    height: 22px;
    border-radius: 50%;
    background: var(--brand-teal);
  }
  .brand-name {
    font-weight: 600;
    font-size: 38px;
    letter-spacing: 1px;
    color: var(--brand-teal);
    line-height: 1;
  }
  .backdrop-mark {
    position: absolute;
    left: 496px;
    top: 600px;
    width: 400px;
    height: 400px;
    transform: translate(-50%, -50%);
    border-radius: 50%;
    background: radial-gradient(circle, var(--mark-tint) 0%, rgba(228,235,243,0.35) 60%, rgba(228,235,243,0) 100%);
  }
  .footer {
    position: absolute;
    left: 0;
    right: 0;
    top: 1108px;
    text-align: center;
  }
  .footer-address {
    font-size: 16px;
    font-weight: 400;
    letter-spacing: 0.5px;
    margin: 0 0 7px;
    line-height: 1.2;
  }
  .footer-contacts {
    display: flex;
    justify-content: center;
    align-items: center;
    gap: 12px;
    font-size: 13px;
    letter-spacing: 0.3px;
    margin: 0;
    line-height: 1.2;
  }
  .contact-item {
    display: inline-flex;
    align-items: center;
    gap: 6px;
  }
  .contact-icon {
    width: 12px;
    height: 12px;
    fill: none;
    stroke: var(--brand-green);
    stroke-width: 1.6;
  }
</style>
</head>
<body>
  <main class="letterhead">
    <header class="brand">
      <span class="brand-dot" aria-hidden="true"></span>
      <span class="brand-name">Hearthside Vet Care</span>
    </header>

    <div class="backdrop-mark" role="img" aria-label="Faint brand watermark area"></div>

    <footer class="footer">
      <p class="footer-address">PO Box 5520 Maple Ridge QLD 4070</p>
      <p class="footer-contacts">
        <span class="contact-item">
          <svg class="contact-icon" viewBox="0 0 16 16" aria-hidden="true"><path d="M4 1.5 L6.5 4.5 L5 6.5 Q6.5 9.5 9.5 11 L11.5 9.5 L14.5 12 L13 14.5 Q6 14 1.5 3 Z"/></svg>
          0400123987
        </span>
        <span class="contact-item">
          <svg class="contact-icon" viewBox="0 0 16 16" aria-hidden="true"><rect x="1.5" y="3.5" width="13" height="9" rx="1"/><path d="M1.5 4 L8 9 L14.5 4"/></svg>
          HELLO@HEARTHSIDEVETCARE.COM.AU
        </span>
        <span class="contact-item">
          <svg class="contact-icon" viewBox="0 0 16 16" aria-hidden="true"><circle cx="8" cy="8" r="6.5"/><ellipse cx="8" cy="8" rx="3" ry="6.5"/><path d="M1.5 8 H14.5"/></svg>
          WWW.HEARTHSIDEVETCARE.COM.AU
        </span>
      </p>
    </footer>
  </main>
</body>
</html>
```